Video Learning Web Application Site Design

We are a new company that produce and distribute educational videos using a subscription model on our website. The videos are streamed on our website and users can tailor their own course packages by creating playlists. Each video-lesson are also split into several smaller segments, and it should be easy to find and play those segments.

Please note that both the screenshots and wireframes provided are only how it looks right now, if you as the designer have a better idea on how to present it then please share it.
Updates

Please view the screenshots as well, I believe I forgot to include two buttons on the wireframes that should be on the Our Courses page. Also, there is no need to make a carbon copy of the wireframes/screenshots, I'd like you designers to come up with a better way of displaying the information if possible. For inspiration you can look at sites like ClipHarbor (I like the simplicity of their design) and to some extent the Tessel UI where they divide different areas of the page into clear "zones".

Thanks,

Project Deadline Extended
Reason: I have to extend the deadline because I've been really ill the last week. Will go through the current submissions now and provide feedback and looking forward to more submissions.

Target Market(s)

College and University students. Professionals wanting to expand their knowledge and people that want to learn new skills to get a promotion/new job.

Industry/Entity Type

Tailor

Requirements
Must have
• Must include the logo from the file "brainlark-logo".
• Should include two pages, one of the video-player page and one of the course list.
• Try to incorporate the colors from the logo.
• Please note: If you look at the video-player.png file just below "Åpne Tabell, lage..." there are two rows, those are sub-parts of the lesson. Both these and the main lesson itself must have some easy way to Play and Add to Playlist.
Nice to have
• We prefer flat design, with simple and clean icons. Don't overdo the colors, stay within 3-4 colors with variations of them.
Should not have
• 3D-like elements, lot of shadows or hard to ready text.

```html
<!DOCTYPE html>
<html lang="en">
<head>
<meta charset="utf-8">
<title>brainlark – Your Courses</title>
<link href="https://fonts.googleapis.com/css2?family=Ubuntu:wght@300;400;500;700&display=swap" rel="stylesheet">
<style>
:root{
  --navy:#0d587e;
  --blue:#1089c2;
  --sky:#9fd3ea;
  --sky-row:#a8d8ee;
  --ink:#1e1e1e;
  --side:#1b1b1b;
  --side-line:#2c2c2c;
  --grey-bg:#f2f2f2;
  --muted:#8b8b8b;
  --orange:#e8891f;
  --green:#a5c85a;
  --coral:#ea6f6c;
  --rule:#d9d9d9;
}
*{box-sizing:border-box;margin:0;padding:0}
html,body{width:1200px;height:752px;overflow:hidden;background:#fff}
body{position:relative;font-family:"Ubuntu",sans-serif;color:var(--ink)}
.abs{position:absolute}

/* header */
.brand{left:18px;top:18px;display:flex;align-items:center;gap:10px}
.brand-dot{width:40px;height:40px;border-radius:50%;background:var(--navy)}
.brand-name{font-size:40px;font-weight:700;color:var(--navy);letter-spacing:-0.5px;line-height:1}
.session{left:858px;top:18px;font-size:12px;color:#333}
.logout{left:998px;top:11px;width:111px;height:24px;background:var(--green);color:#fff;font-size:12px;display:flex;align-items:center;justify-content:center}
.topnav{left:645px;top:48px;width:465px;height:32px;background:var(--navy);display:flex;align-items:center}
.topnav .menu{width:36px;height:32px;display:flex;align-items:center;justify-content:center;border-right:1px solid #0a4866}
.topnav a{color:#fff;font-weight:500;font-size:13px;text-decoration:none;padding:0 12px;height:32px;line-height:32px;border-right:1px solid #0a4866}
.search{left:944px;top:51px;width:134px;height:26px;background:#fff}
.search-btn{left:1079px;top:51px;width:28px;height:26px;background:var(--blue);display:flex;align-items:center;justify-content:center}
.header-rule{left:0;top:78px;width:1200px;height:4px;background:var(--navy)}

/* sidebar */
.sidebar{left:0;top:82px;width:262px;height:670px;background:var(--side)}
.side-head{height:36px;padding-left:20px;font-size:19px;font-weight:300;color:#fff;display:flex;align-items:center;border-bottom:1px solid var(--side-line)}
.side-head.modules{height:40px;background:var(--navy);border-bottom:1px solid #0a4866}
.side-head.lists{height:40px}
.side-item{position:relative;height:32px;display:flex;align-items:center;font-size:12px;color:#fff;border-bottom:1px solid var(--side-line)}
.side-item .ico{width:37px;height:100%;display:flex;align-items:center;justify-content:center;border-right:1px solid var(--side-line)}
.side-item .label{padding-left:10px;flex:1}
.side-item.first{height:36px}
.modules-group .side-item{background:var(--navy);border-bottom:1px solid #0a4866}
.modules-group .side-item .ico{border-right:1px solid #0a4866}
.modules-group .side-item.active .label{background:var(--blue);height:100%;display:flex;align-items:center}
.side-item.active::after{content:"";position:absolute;right:0;top:9px;border:7px solid transparent;border-right-color:#fff}
.count{width:23px;height:17px;margin-right:8px;font-size:11px;color:#fff;display:flex;align-items:center;justify-content:center;background:var(--orange)}
.count.green{background:var(--green)}

/* main */
.page-title{left:286px;top:100px;font-size:26px;font-weight:300}
.player{left:284px;top:142px;width:397px;height:228px;background:#000}
.player-frame{position:absolute;left:0;top:0;width:397px;height:196px;background:linear-gradient(120deg,#d9cfc2 0%,#b88a62 35%,#8f5a3c 55%,#d7b98e 75%,#f0e8de 100%)}
.controls{position:absolute;left:0;top:196px;width:397px;height:32px;display:flex;align-items:center;padding:0 10px;gap:10px;color:#fff;font-size:10px}
.track{flex:1;height:4px;background:#2a2a2a;position:relative}
.track span{position:absolute;left:0;top:0;height:4px;width:43%;background:var(--blue)}

.course-thumb{left:284px;top:387px;width:48px;height:48px}
.thumb{background:linear-gradient(135deg,#6f99ad,#d7e4ea 50%,#7aa2b4)}
.course-title{left:344px;top:384px;font-size:23px;font-weight:300;white-space:nowrap;line-height:28px}
.course-sub{left:345px;top:412px;font-size:11px;color:var(--muted);line-height:13px}
.remove{left:589px;top:387px;width:93px;height:20px;background:var(--coral);color:#fff;font-size:10px;display:flex;align-items:center;justify-content:center}

.explore-head{left:701px;top:142px;width:409px;height:36px;background:var(--sky);display:flex;align-items:center;color:#fff;font-weight:500;font-size:13px}
.explore-head .menu{width:48px;display:flex;justify-content:center;border-right:1px solid #b9e1f2;height:100%;align-items:center}
.explore-head .name{padding-left:12px}
.col-label{font-size:12px;color:#333}
.link-list{list-style:none;border-top:1px solid var(--rule)}
.link-list li{height:19px;display:flex;align-items:center;font-size:11px;color:var(--navy);border-bottom:1px solid var(--rule);white-space:nowrap}
.link-list li .mark{width:30px;display:flex;justify-content:center}
.link-list li.on{background:var(--sky-row)}
.link-list li.on .mark{background:#fff;height:100%;align-items:center}

/* lower zone */
.lower{left:262px;top:454px;width:938px;height:298px;background:var(--grey-bg)}
.show-cues{left:284px;top:462px;width:110px;height:20px;background:var(--orange);color:#fff;font-size:10px;display:flex;align-items:center;justify-content:center}
.pager{left:587px;top:462px;width:94px;height:20px;background:#555;color:#fff;font-size:9.5px;display:flex;align-items:center;justify-content:space-between}
.pager span{width:17px;height:100%;display:flex;align-items:center;justify-content:center;background:#666}
.tree{left:284px;top:487px;width:385px}
.tree .row{display:flex;align-items:center;border-bottom:1px solid var(--rule);font-size:11px}
.tree .parent{height:30px;font-size:12.5px}
.tree .parent .caret{width:28px;display:flex;justify-content:center}
.tree .child{height:19.2px;margin-left:44px}
.tree .child .caret{width:0;position:relative;left:-15px}
.tree .child .star{width:22px;display:flex;justify-content:center}
.tree .child.on{background:#e4e4e4}
.scroll{left:676px;top:495px;width:5px;height:239px;background:#dcdcdc}
.scroll span{display:block;height:103px;background:#9a9a9a}

.related-title{left:706px;top:466px;font-size:18px;font-weight:300}
.rel{display:flex;gap:10px;width:230px}
.rel .thumb{width:48px;height:48px;flex:none}
.rel h3{font-size:14px;font-weight:300;color:#555;line-height:16px;margin-top:3px;white-space:nowrap}
.rel p{font-size:9.5px;color:var(--muted);line-height:12px}
.stars{display:flex;gap:2px;margin-top:1px}
</style>
</head>
<body>
<svg width="0" height="0" style="position:absolute">
  <defs>
    <symbol id="star" viewBox="0 0 20 20"><polygon points="10,1 12.6,7 19,7.5 14,11.6 15.6,18 10,14.6 4.4,18 6,11.6 1,7.5 7.4,7" fill="#e8891f"/></symbol>
    <symbol id="star-o" viewBox="0 0 20 20"><polygon points="10,1 12.6,7 19,7.5 14,11.6 15.6,18 10,14.6 4.4,18 6,11.6 1,7.5 7.4,7" fill="none" stroke="#e8891f" stroke-width="1.6"/></symbol>
    <symbol id="tri" viewBox="0 0 10 10"><polygon points="2,1 9,5 2,9" fill="currentColor"/></symbol>
    <symbol id="tri-d" viewBox="0 0 10 10"><polygon points="1,2 9,2 5,9" fill="currentColor"/></symbol>
    <symbol id="circ-play" viewBox="0 0 20 20"><circle cx="10" cy="10" r="8" fill="none" stroke="#fff" stroke-width="2"/><polygon points="8,6 14,10 8,14" fill="#fff"/></symbol>
    <symbol id="windows" viewBox="0 0 20 20"><rect x="2" y="7" width="10" height="10" fill="none" stroke="#fff" stroke-width="2"/><rect x="8" y="2" width="10" height="10" fill="none" stroke="#fff" stroke-width="2"/></symbol>
    <symbol id="hamb" viewBox="0 0 14 12"><rect y="1" width="14" height="2" fill="#fff"/><rect y="5" width="14" height="2" fill="#fff"/><rect y="9" width="14" height="2" fill="#fff"/></symbol>
    <symbol id="dl" viewBox="0 0 16 16"><path d="M2 9v5h12V9" fill="none" stroke="#7fbfdf" stroke-width="2"/><path d="M8 1v8M5 6l3 3 3-3" fill="none" stroke="#7fbfdf" stroke-width="2"/></symbol>
  </defs>
</svg>

<header>
  <div class="abs brand"><span class="brand-dot"></span><span class="brand-name">brainlark</span></div>
  <div class="abs session">Logged in as Fernwick</div>
  <div class="abs logout">Log Out</div>
  <nav class="abs topnav">
    <span class="menu"><svg width="13" height="11"><use href="#hamb"/></svg></span>
    <a>About</a><a>Videos</a><a>Help</a><a>Options</a>
  </nav>
  <div class="abs search"></div>
  <div class="abs search-btn"><svg width="20" height="20" viewBox="0 0 20 20"><circle cx="8.5" cy="8.5" r="6" fill="none" stroke="#fff" stroke-width="2.4"/><line x1="13" y1="13" x2="18" y2="18" stroke="#fff" stroke-width="2.6"/></svg></div>
  <div class="abs header-rule"></div>
</header>

<aside class="abs sidebar">
  <div class="side-head">Introduction</div>
  <div class="side-item first"><span class="ico"><svg width="18" height="18" viewBox="0 0 20 20"><circle cx="10" cy="10" r="8" fill="none" stroke="#fff" stroke-width="2"/><path d="M6 6l5 2 2 5-5-2z" fill="#fff"/></svg></span><span class="label">Introduction</span><span class="count">12</span></div>
  <div class="side-head modules">Modules</div>
  <div class="modules-group">
    <div class="side-item"><span class="ico"><svg width="17" height="17"><use href="#windows"/></svg></span><span class="label">Our Courses</span></div>
    <div class="side-item active"><span class="ico"><svg width="17" height="17" viewBox="0 0 20 20"><circle cx="10" cy="6" r="4" fill="none" stroke="#fff" stroke-width="2"/><path d="M2 18c0-4 3.5-6 8-6s8 2 8 6z" fill="none" stroke="#fff" stroke-width="2"/></svg></span><span class="label">Your Courses</span></div>
    <div class="side-item"><span class="ico"><svg width="17" height="17"><use href="#windows"/></svg></span><span class="label">Lorem Courses</span></div>
  </div>
  <div class="side-head lists">Playlists</div>
  <div class="side-item"><span class="ico"><svg width="18" height="18"><use href="#circ-play"/></svg></span><span class="label">My Playlist 01</span><span class="count">12</span></div>
  <div class="side-item"><span class="ico"><svg width="18" height="18"><use href="#circ-play"/></svg></span><span class="label">Lorem Playlist</span><span class="count green">4</span></div>
  <div class="side-item"><span class="ico"><svg width="18" height="18"><use href="#circ-play"/></svg></span><span class="label">Impsum Plays</span></div>
  <div class="side-item"><span class="ico"><svg width="18" height="18"><use href="#circ-play"/></svg></span><span class="label">PlayList Doner 02</span><span class="count">3</span></div>
</aside>

<main>
  <h1 class="abs page-title">Your Courses</h1>

  <div class="abs player">
    <div class="player-frame" role="img" aria-label="Video frame: group of smiling students holding books and notebooks"></div>
    <div class="controls">
      <svg width="12" height="14" viewBox="0 0 10 12"><polygon points="0,0 10,6 0,12" fill="#fff"/></svg>
      <div class="track"><span></span></div>
      <span>1:04/4:30</span>
      <svg width="16" height="14" viewBox="0 0 16 14"><polygon points="0,4 4,4 9,0 9,14 4,10 0,10" fill="#fff"/><path d="M11 4q2 3 0 6M13 2q4 5 0 10" stroke="#fff" fill="none" stroke-width="1.4"/></svg>
      <svg width="14" height="14" viewBox="0 0 14 14" fill="none" stroke="#fff" stroke-width="2"><path d="M1 5V1h4M9 1h4v4M13 9v4H9M5 13H1V9"/></svg>
    </div>
  </div>

  <div class="abs course-thumb thumb" role="img" aria-label="Course artwork: abstract figure in motion"></div>
  <h2 class="abs course-title">Tabula 2013 - Beginner</h2>
  <p class="abs course-sub">Lorem Impsum proin<br>Impsum Text</p>
  <div class="abs remove">Remove Course</div>

  <div class="abs explore-head"><span class="menu"><svg width="14" height="11"><use href="#hamb"/></svg></span><span class="name">Explore Item 1</span></div>

  <div class="abs" style="left:718px;top:194px;width:164px">
    <div class="col-label" style="margin-bottom:7px">Cues</div>
    <ul class="link-list">
      <li><span class="mark" style="color:var(--sky)"><svg width="8" height="8"><use href="#tri"/></svg></span>Child lorem 1</li>
      <li class="on"><span class="mark" style="color:var(--sky)"><svg width="8" height="8"><use href="#tri"/></svg></span>Child Impsum 2</li>
      <li><span class="mark" style="color:var(--sky)"><svg width="8" height="8"><use href="#tri"/></svg></span>Child proin 3</li>
      <li><span class="mark" style="color:var(--sky)"><svg width="8" height="8"><use href="#tri"/></svg></span>Child gravida 4</li>
    </ul>
  </div>
  <div class="abs" style="left:912px;top:194px;width:189px">
    <div class="col-label" style="margin-bottom:7px">Files</div>
    <ul class="link-list">
      <li><span class="mark" style="width:28px"><svg width="13" height="13"><use href="#dl"/></svg></span>Download Lessons file (xls)</li>
      <li><span class="mark" style="width:28px"><svg width="13" height="13"><use href="#dl"/></svg></span>Download Study material (doc)</li>
    </ul>
  </div>

  <section class="abs lower"></section>
  <div class="abs show-cues">Show All Cues</div>
  <div class="abs pager"><span><svg width="6" height="8" viewBox="0 0 6 8"><polygon points="6,0 0,4 6,8" fill="#bbb"/></svg></span>1-10 of 50<span><svg width="6" height="8" viewBox="0 0 6 8"><polygon points="0,0 6,4 0,8" fill="#bbb"/></svg></span></div>

  <div class="abs tree" style="color:#aaa">
    <div class="row parent"><span class="caret"><svg width="9" height="9"><use href="#tri-d"/></svg></span><span style="color:var(--ink)">Item 1</span></div>
    <div class="row child"><span class="caret"><svg width="8" height="8"><use href="#tri"/></svg></span><span class="star"><svg width="12" height="12"><use href="#star-o"/></svg></span><span style="color:var(--ink)">Child lorem 1</span></div>
    <div class="row child on"><span class="star"><svg width="12" height="12"><use href="#star"/></svg></span><span style="color:var(--ink)">Child Impsum 2</span></div>
    <div class="row child"><span class="caret"><svg width="8" height="8"><use href="#tri"/></svg></span><span class="star"><svg width="12" height="12"><use href="#star"/></svg></span><span style="color:var(--ink)">Child proin 3</span></div>
    <div class="row child"><span class="star"><svg width="12" height="12"><use href="#star"/></svg></span><span style="color:var(--ink)">Child gravida 4</span></div>
    <div class="row parent"><span class="caret"><svg width="8" height="8"><use href="#tri"/></svg></span><span style="color:var(--ink)">Item 2</span></div>
    <div class="row parent"><span class="caret"><svg width="9" height="9"><use href="#tri-d"/></svg></span><span style="color:var(--ink)">Item 3</span></div>
    <div class="row child"><span class="caret"><svg width="8" height="8"><use href="#tri"/></svg></span><span class="star"><svg width="12" height="12"><use href="#star-o"/></svg></span><span style="color:var(--ink)">Child lorem 1</span></div>
    <div class="row child"><span class="star"><svg width="12" height="12"><use href="#star"/></svg></span><span style="color:var(--ink)">Child Impsum 2</span></div>
    <div class="row child"><span class="caret"><svg width="8" height="8"><use href="#tri"/></svg></span><span class="star"><svg width="12" height="12"><use href="#star"/></svg></span><span style="color:var(--ink)">Child proin 3</span></div>
    <div class="row child" style="border-bottom:0"><span class="star"><svg width="12" height="12"><use href="#star"/></svg></span><span style="color:var(--ink)">Child gravida 4</span></div>
  </div>
  <div class="abs scroll"><span></span></div>

  <h2 class="abs related-title">Related Courses</h2>

  <div class="abs rel" style="left:708px;top:497px"><div class="thumb" role="img" aria-label="Course artwork"></div><div><h3>Slidecraft 2013 Expert</h3><p>June 2013</p><div class="stars"><svg width="10" height="10"><use href="#star"/></svg><svg width="10" height="10"><use href="#star"/></svg><svg width="10" height="10"><use href="#star"/></svg><svg width="10" height="10"><use href="#star"/></svg><svg width="10" height="10"><use href="#star-o"/></svg></div></div></div>
  <div class="abs rel" style="left:945px;top:497px"><div class="thumb" role="img" aria-label="Course artwork"></div><div><h3>Slidecraft 2013 Expert</h3><p>June 2013</p><div class="stars"><svg width="10" height="10"><use href="#star"/></svg><svg width="10" height="10"><use href="#star"/></svg><svg width="10" height="10"><use href="#star"/></svg><svg width="10" height="10"><use href="#star"/></svg><svg width="10" height="10"><use href="#star-o"/></svg></div></div></div>
  <div class="abs rel" style="left:708px;top:559px"><div class="thumb" role="img" aria-label="Course artwork"></div><div><h3>Slidecraft 2013 Expert</h3><p>June 2013</p><div class="stars"><svg width="10" height="10"><use href="#star"/></svg><svg width="10" height="10"><use href="#star"/></svg><svg width="10" height="10"><use href="#star"/></svg><svg width="10" height="10"><use href="#star"/></svg><svg width="10" height="10"><use href="#star-o"/></svg></div></div></div>
  <div class="abs rel" style="left:945px;top:559px"><div class="thumb" role="img" aria-label="Course artwork"></div><div><h3>Slidecraft 2013 Expert</h3><p>June 2013</p><div class="stars"><svg width="10" height="10"><use href="#star"/></svg><svg width="10" height="10"><use href="#star"/></svg><svg width="10" height="10"><use href="#star"/></svg><svg width="10" height="10"><use href="#star"/></svg><svg width="10" height="10"><use href="#star-o"/></svg></div></div></div>
  <div class="abs rel" style="left:708px;top:619px"><div class="thumb" role="img" aria-label="Course artwork"></div><div><h3>Slidecraft 2013 Expert</h3><p>June 2013</p><div class="stars"><svg width="10" height="10"><use href="#star"/></svg><svg width="10" height="10"><use href="#star"/></svg><svg width="10" height="10"><use href="#star"/></svg><svg width="10" height="10"><use href="#star"/></svg><svg width="10" height="10"><use href="#star-o"/></svg></div></div></div>
  <div class="abs rel" style="left:945px;top:619px"><div class="thumb" role="img" aria-label="Course artwork"></div><div><h3>Slidecraft 2013 Expert</h3><p>June 2013</p><div class="stars"><svg width="10" height="10"><use href="#star"/></svg><svg width="10" height="10"><use href="#star"/></svg><svg width="10" height="10"><use href="#star"/></svg><svg width="10" height="10"><use href="#star"/></svg><svg width="10" height="10"><use href="#star-o"/></svg></div></div></div>
  <div class="abs rel" style="left:708px;top:684px"><div class="thumb" role="img" aria-label="Course artwork"></div><div><h3>Slidecraft 2013 Expert</h3><p>June 2013</p><div class="stars"><svg width="10" height="10"><use href="#star"/></svg><svg width="10" height="10"><use href="#star"/></svg><svg width="10" height="10"><use href="#star"/></svg><svg width="10" height="10"><use href="#star"/></svg><svg width="10" height="10"><use href="#star-o"/></svg></div></div></div>
  <div class="abs rel" style="left:945px;top:684px"><div class="thumb" role="img" aria-label="Course artwork"></div><div><h3>Slidecraft 2013 Expert</h3><p>June 2013</p><div class="stars"><svg width="10" height="10"><use href="#star"/></svg><svg width="10" height="10"><use href="#star"/></svg><svg width="10" height="10"><use href="#star"/></svg><svg width="10" height="10"><use href="#star"/></svg><svg width="10" height="10"><use href="#star-o"/></svg></div></div></div>
</main>
</body>
</html>
```